Business Card for Vorla Parts Wholesale supplier

Hi There! I need a new business card for our company. We are specialized in selling Vorla parts, mostly we sell new LCD screens for Zelnar and Drelks. I would like to see that back in the design.

You can find the colors and logo's on our website: www.hartuvo.nl

Industry/Entity Type

Business

Contact Information for Business Card

My Details:
Tobias Lindqvist

Phone: 0031687203316
E-mail: Tobias@hartuvo.nl

Slogan: "Because Quality Matters"

Font styles to use
Sans Serif

Colors

Designer to choose colors to be used in the design.

Requirements
Must have
• A Black backside with the Hartuvo logo on it. The front side should be clean with only my contact details.
• But I'm also open for something really different or awesome!
Nice to have
• Remember that we are in the parts & repairing industry, So i'll be handing those business cards mainly to repair companies. Maybe you can do something with that thought :)

```html
<!DOCTYPE html>
<html lang="en">
<head>
<meta charset="utf-8">
<title>Hartuvo – Business Card</title>
<link href="https://fonts.googleapis.com/css2?family=Open+Sans:wght@400;600;800&display=swap" rel="stylesheet">
<style>
  :root {
    --page-bg: #d9d4cc;
    --card-bg: #eeece8;
    --ink: #141414;
    --orange: #d2461c;
    --orange-light: #e2622e;
    --orange-deep: #a8260c;
    --panel-dark: #1b1b1b;
    --panel-mid: #2a2a2a;
    --text-light: #ece6dc;
    --text-contact: #d8c9c2;
  }
  * { margin: 0; padding: 0; box-sizing: border-box; }
  html, body {
    width: 1200px; height: 970px; overflow: hidden;
    background: var(--page-bg);
    font-family: "Open Sans", Arial, sans-serif;
  }
  .card {
    position: absolute; left: 80px; top: 189px;
    width: 1040px; height: 592px;
    background: linear-gradient(160deg, #f4f2ef 0%, var(--card-bg) 60%, #e4e1dc 100%);
    overflow: hidden;
    box-shadow: 0 10px 30px rgba(0,0,0,0.18);
  }
  .brand {
    position: absolute; left: 55px; top: 72px;
    display: flex; align-items: center; gap: 26px;
  }
  .brand-square {
    width: 120px; height: 120px; background: var(--orange);
  }
  .brand-name {
    font-weight: 800; font-size: 118px; line-height: 1;
    color: var(--ink); letter-spacing: 1px;
  }
  .name-band {
    position: absolute; left: 0; top: 303px;
    width: 820px; height: 58px;
    background: linear-gradient(90deg, var(--orange-light) 0%, var(--orange) 50%, var(--orange-deep) 100%);
    clip-path: polygon(0 0, 100% 0, 96% 100%, 0 100%);
  }
  .person-name {
    position: absolute; left: 49px; top: 8px;
    font-weight: 600; font-size: 34px; color: var(--text-light);
  }
  .info-panel {
    position: absolute; left: 0; top: 361px;
    width: 1040px; height: 231px;
    background: linear-gradient(180deg, var(--panel-dark) 0%, var(--panel-mid) 100%);
  }
  .slogan {
    position: absolute; left: 52px; top: 24px;
    font-size: 28px; color: var(--text-light);
  }
  .contact-list {
    position: absolute; left: 54px; top: 86px; list-style: none;
  }
  .contact-item {
    display: flex; align-items: center; gap: 12px;
    height: 35px; font-size: 28px; color: var(--text-contact);
  }
  .contact-icon { width: 28px; height: 28px; }
  .accent-circle {
    position: absolute; left: 760px; top: 310px;
    width: 330px; height: 330px; border-radius: 50%;
    background: radial-gradient(circle at 50% 45%, var(--orange-light) 0%, var(--orange) 55%, var(--orange-deep) 100%);
  }
</style>
</head>
<body>
  <div class="card">
    <div class="brand">
      <div class="brand-square"></div>
      <div class="brand-name">hartuvo</div>
    </div>

    <div class="info-panel">
      <p class="slogan">Because Quality Matters</p>
      <ul class="contact-list">
        <li class="contact-item">
          <svg class="contact-icon" viewBox="0 0 28 28" aria-hidden="true">
            <rect width="28" height="28" fill="var(--orange)"/>
            <path d="M6 11c0-3 4-5 8-5s8 2 8 5l-3 1-1-2h-8l-1 2z" fill="#1b1b1b"/>
            <rect x="8" y="13" width="12" height="9" rx="1" fill="#1b1b1b"/>
          </svg>
          <span>0031687203316</span>
        </li>
        <li class="contact-item">
          <svg class="contact-icon" viewBox="0 0 28 28" aria-hidden="true">
            <rect width="28" height="28" fill="var(--orange)"/>
            <rect x="5" y="8" width="18" height="12" fill="none" stroke="#1b1b1b" stroke-width="2"/>
            <path d="M5 8l9 7 9-7" fill="none" stroke="#1b1b1b" stroke-width="2"/>
          </svg>
          <span>Tobias@hartuvo.nl</span>
        </li>
        <li class="contact-item">
          <svg class="contact-icon" viewBox="0 0 28 28" aria-hidden="true">
            <rect width="28" height="28" fill="var(--orange)"/>
            <circle cx="14" cy="14" r="8" fill="none" stroke="#1b1b1b" stroke-width="2"/>
            <ellipse cx="14" cy="14" rx="3.5" ry="8" fill="none" stroke="#1b1b1b" stroke-width="1.5"/>
            <line x1="6" y1="14" x2="22" y2="14" stroke="#1b1b1b" stroke-width="1.5"/>
          </svg>
          <span>www.hartuvo.nl</span>
        </li>
      </ul>
    </div>

    <div class="name-band">
      <span class="person-name">Tobias Lindqvist</span>
    </div>

    <div class="accent-circle"></div>
  </div>
</body>
</html>
```